Best local air conditioning and heating contractor

We need a website design for a new company in Tampa Bay called Coastal Breeze Cooling Company. We provide superior services for residential and commercial properties as well as maintenance and installing HVAC systems. We also want to sell equipment, parts and filter on the website as well. We want it easy to use for customers. Rich with content and keywords for our area.

Target Market(s)

homeowners in Tampa Bay

Industry/Entity Type

HVAC air conditioning and heating

Coding

Coded - Design and coding required

Number of Pages Required

5+ page

Font styles to use
Sans Serif

Requirements
Nice to have
• would like the colors to be same as logo

```html
<!DOCTYPE html>
<html lang="en">
<head>
<meta charset="utf-8">
<title>Coastal Breeze Cooling Company</title>
<link href="https://fonts.googleapis.com/css2?family=Audiowide&family=Oswald:wght@300;400;500&family=Poppins:wght@400;500&display=swap" rel="stylesheet">
<style>
:root{
  --navy:#1f2f6b;
  --navy-dark:#1a2a61;
  --red:#d9232d;
  --white:#ffffff;
  --grey-bg:#f7f7f8;
  --grey-band:#e8e8ea;
  --text:#333333;
  --muted:#8a8a8a;
}
*{box-sizing:border-box;margin:0;padding:0}
html,body{width:1200px;height:4310px;overflow:hidden}
body{position:relative;background:var(--white);font-family:'Oswald',sans-serif;color:var(--text)}
.abs{position:absolute}
.display{font-family:'Audiowide',sans-serif;text-transform:uppercase;letter-spacing:2px}
.btn-skew{position:absolute;display:flex;align-items:center;justify-content:center;color:var(--white);font-family:'Oswald',sans-serif;font-weight:500;font-size:24px;clip-path:polygon(6% 0,100% 0,94% 100%,0 100%)}
.btn-navy{background:var(--navy)}
.btn-red{background:var(--red)}

/* header */
.site-header{position:absolute;top:0;left:0;width:1200px;height:117px;background:var(--white);border-top:4px solid var(--red);box-shadow:0 2px 6px rgba(0,0,0,.1);z-index:2}
.brand{position:absolute;left:100px;top:22px;display:flex;align-items:center;gap:12px}
.brand-mark{width:26px;height:26px;background:var(--red)}
.brand-name{font-family:'Oswald',sans-serif;font-weight:500;color:var(--navy);font-size:22px;line-height:1.05;text-transform:uppercase}
.topbar{position:absolute;left:372px;top:-4px;width:828px;height:62px;background:var(--navy);clip-path:polygon(3% 0,100% 0,100% 100%,0 100%);display:flex;align-items:center;padding-left:38px;gap:20px;color:var(--white);font-size:14px;font-weight:300}
.topbar-item{display:flex;align-items:center;gap:14px}
.topbar-icon{width:30px;height:30px;border-radius:50%;background:var(--red);display:flex;align-items:center;justify-content:center}
.topbar-sep{width:1px;height:20px;background:rgba(255,255,255,.6)}
.main-nav{position:absolute;top:70px;left:437px;display:flex;gap:66px;font-size:18px;color:var(--text)}

/* hero */
.hero{position:absolute;top:117px;left:0;width:1200px;height:488px;background:linear-gradient(90deg,#1d2532 0%,#36404f 45%,#6e7a86 70%,#9aa7b2 100%)}
.hero-title{position:absolute;left:100px;top:130px;color:var(--white);font-size:50px;line-height:60px}
.hero-text{position:absolute;left:100px;top:263px;width:520px;color:var(--white);font-size:12px;font-weight:300;line-height:22px}
.hero .btn-skew{left:86px;top:333px;width:208px;height:55px}

/* consultation */
.consult{position:absolute;top:605px;left:0;width:1200px;height:127px;background:var(--navy);display:flex;align-items:center}
.consult-title{position:absolute;left:100px;top:36px;color:var(--white);font-size:18px;line-height:26px}
.consult-field{position:absolute;top:43px;width:172px;height:40px;border-radius:20px;background:var(--white);font-size:12px;font-weight:300;padding:11px 16px;color:#444}
.consult-submit{position:absolute;left:930px;top:43px;width:172px;height:40px;border-radius:20px;background:var(--red);color:var(--white);font-size:18px;display:flex;align-items:center;justify-content:center}

/* section head */
.section-head{position:absolute;left:0;width:1200px;text-align:center}
.section-title{color:var(--navy);font-size:40px;letter-spacing:3px}
.section-desc{margin:14px auto 0;width:760px;color:var(--muted);font-size:13px;font-weight:300;line-height:24px}

/* services */
.services{position:absolute;top:732px;left:0;width:1200px;height:600px;background:var(--grey-bg)}
.service-card{position:absolute;top:271px;width:415px;height:252px;border-radius:6px;overflow:hidden}
.service-card .label{position:absolute;left:22px;bottom:18px;color:var(--white);font-size:27px}
.service-card .go{position:absolute;right:22px;bottom:16px;width:40px;height:40px;border-radius:50%;background:var(--red);border:3px solid rgba(255,255,255,.7);display:flex;align-items:center;justify-content:center}
.team-photo{position:absolute;top:1220px;left:0;width:1200px;height:640px;background:linear-gradient(100deg,#e7ebef 0%,#c9d3dc 40%,#5a7db8 70%,#3a5fa2 100%)}
.estimate{left:474px;top:1288px;width:271px;height:54px}

/* about */
.about-photo{position:absolute;left:135px;top:1995px;width:440px;height:433px;border-radius:0 80px 0 80px;background:linear-gradient(135deg,#c98d68 0%,#9aa3ad 50%,#d7dbe0 100%)}
.about-accent{position:absolute;left:98px;top:2300px;width:157px;height:163px;background:var(--red);border-radius:12px}
.body-copy{font-size:14px;font-weight:300;line-height:29px;color:#555}
.about-text{position:absolute;left:637px;top:2048px;width:470px}
.about-text p+p{margin-top:24px}

/* sell equipment */
.equipment{position:absolute;top:2565px;left:0;width:1200px;height:530px;background:var(--grey-band);overflow:hidden}
.equipment-title{position:absolute;left:98px;top:100px;color:var(--navy);font-size:38px;letter-spacing:3px}
.equipment-text{position:absolute;left:98px;top:170px;width:470px}

/* blog */
.blog-card{position:absolute;top:3345px;width:323px;height:380px;background:var(--white);box-shadow:0 3px 12px rgba(0,0,0,.14)}
.blog-thumb{position:absolute;left:10px;top:5px;width:303px;height:205px;border-radius:0 0 16px 16px;overflow:hidden}
.blog-date{position:absolute;left:20px;bottom:14px;display:flex;align-items:center;gap:14px;color:var(--white);font-family:'Poppins',sans-serif;font-size:14px}
.blog-date i{width:32px;height:32px;border-radius:50%;background:var(--navy);display:flex;align-items:center;justify-content:center}
.blog-title{position:absolute;left:22px;top:232px;font-size:18px;font-weight:500;color:#111}
.blog-excerpt{position:absolute;left:22px;top:270px;width:270px;font-family:'Poppins',sans-serif;font-size:15px;line-height:26px;color:#333}
.blog-more{position:absolute;left:22px;top:338px;font-family:'Poppins',sans-serif;font-weight:500;font-size:14px;color:var(--navy);letter-spacing:.5px}

/* footer */
.site-footer{position:absolute;top:3822px;left:0;width:1200px;height:488px;background:var(--navy);color:var(--white)}
.footer-brand{position:absolute;left:110px;top:150px;display:flex;align-items:center;gap:14px}
.footer-brand .brand-mark{width:30px;height:30px}
.footer-brand .brand-name{color:var(--white);font-size:26px}
.footer-heading{position:absolute;top:68px;font-size:21px;letter-spacing:2px}
.footer-menu{position:absolute;left:502px;top:118px;list-style:none;font-size:16px;font-weight:300;line-height:37px}
.footer-contact{position:absolute;left:752px;top:112px;list-style:none;font-size:18px;font-weight:300}
.footer-contact li{display:flex;gap:26px;align-items:flex-start;margin-bottom:26px;line-height:34px}
.footer-contact svg{flex:none;margin-top:9px}
.footer-rule{position:absolute;left:115px;top:368px;width:975px;height:1px;background:rgba(255,255,255,.5)}
.copyright{position:absolute;left:115px;top:408px;font-size:17px;font-weight:300}
.payments{position:absolute;left:742px;top:408px;display:flex;gap:20px}
.payments span{width:42px;height:22px;border-radius:3px;background:rgba(255,255,255,.85)}
</style>
</head>
<body>

<header class="site-header">
  <div class="brand">
    <span class="brand-mark"></span>
    <span class="brand-name">Coastal Breeze<br>Cooling Company</span>
  </div>
  <div class="topbar">
    <span class="topbar-item"><span class="topbar-icon"><svg width="14" height="12" viewBox="0 0 14 12"><rect x="1" y="1" width="12" height="10" fill="none" stroke="#fff" stroke-width="1.5"/><path d="M1 1l6 5 6-5" fill="none" stroke="#fff" stroke-width="1.5"/></svg></span>info@coastalbreezecooling.com</span>
    <span class="topbar-sep"></span>
    <span class="topbar-item"><span class="topbar-icon"><svg width="14" height="14" viewBox="0 0 24 24"><path fill="#fff" d="M6.6 10.8a15 15 0 006.6 6.6l2.2-2.2c.3-.3.7-.4 1-.2 1.1.4 2.3.6 3.6.6.6 0 1 .4 1 1V20c0 .6-.4 1-1 1A17 17 0 013 4c0-.6.4-1 1-1h3.5c.6 0 1 .4 1 1 0 1.3.2 2.5.6 3.6.1.3 0 .7-.2 1z"/></svg></span>+1 888-888-8888</span>
    <span class="topbar-sep"></span>
    <span class="topbar-item"><span class="topbar-icon"><svg width="12" height="16" viewBox="0 0 12 16"><path fill="#fff" d="M6 0a6 6 0 00-6 6c0 4.5 6 10 6 10s6-5.5 6-10a6 6 0 00-6-6zm0 8.5A2.5 2.5 0 116 3.5a2.5 2.5 0 010 5z"/></svg></span>2522 laboris nisi ut aliquip ex ea 1253</span>
  </div>
  <nav class="main-nav"><span>Home</span><span>About Us</span><span>Our Services</span><span>Sell Equipment</span><span>Contact Us</span></nav>
</header>

<section class="hero" role="img" aria-label="Photo of a smiling HVAC technician in a cap beside an outdoor air conditioning unit">
  <h1 class="hero-title display">Coastal Breeze<br>Cooling</h1>
  <p class="hero-text">Lorem ipsum dolor sit amet, consectetur adipiscing elit, sed do eiusmod tempor incididunt ut labore et dolore magna aliqua. Ut enim ad minim veniam, quis nostrud exercitation ullamco laboris nisi ut aliquip ex ea commodo consequat.</p>
  <span class="btn-skew btn-red">Get Started</span>
</section>

<section class="consult">
  <h2 class="consult-title display">Schedule a Free<br>Consultation</h2>
  <span class="consult-field" style="left:365px">Full Name</span>
  <span class="consult-field" style="left:553px">Email</span>
  <span class="consult-field" style="left:741px">Phone</span>
  <span class="consult-submit">Submit Now</span>
</section>

<section class="services">
  <div class="section-head" style="top:135px">
    <h2 class="section-title display">Our Services</h2>
    <p class="section-desc">Sed ut perspiciatis unde omnis iste natus error sit voluptatem accusantium doloremque laudantium, totam rem aperiam, eaque ipsa quae ab illo inventore veritatis et quasi architecto beatae vitae dicta sunt explicabo.</p>
  </div>
</section>

<div class="team-photo" role="img" aria-label="Photo of two technicians in blue shirts checking an outdoor AC unit with gauges and a clipboard"></div>
<svg class="abs" style="left:0;top:1720px" width="1200" height="145" viewBox="0 0 1200 145" aria-hidden="true">
  <polygon points="0,140 600,22 1200,140 1200,145 0,145" fill="#fff"/>
  <polygon points="0,135 600,0 1200,135 1200,140 600,22 0,140" fill="#d9232d"/>
</svg>

<div class="service-card" style="left:165px;top:1003px;background:linear-gradient(180deg,#dfe7df 0%,#7b9a6e 55%,#4d5b4b 100%)" role="img" aria-label="Photo of a residential garden with an outdoor unit">
  <span class="label">Residential</span>
  <span class="go"><svg width="14" height="14" viewBox="0 0 14 14"><path d="M3 3l4 4-4 4M7 3l4 4-4 4" fill="none" stroke="#fff" stroke-width="2"/></svg></span>
</div>
<div class="service-card" style="left:621px;top:1003px;background:linear-gradient(135deg,#9fb3cf 0%,#3b5a92 55%,#213d78 100%)" role="img" aria-label="Photo of AC units mounted on a commercial building wall">
  <span class="label">Commercial Properties</span>
  <span class="go"><svg width="14" height="14" viewBox="0 0 14 14"><path d="M3 3l4 4-4 4M7 3l4 4-4 4" fill="none" stroke="#fff" stroke-width="2"/></svg></span>
</div>
<span class="btn-skew btn-navy estimate">Get A Free Estimate</span>

<div class="section-head" style="top:1866px">
  <h2 class="section-title display">About Us</h2>
  <p class="section-desc">Sed ut perspiciatis unde omnis iste natus error sit voluptatem accusantium doloremque laudantium, totam rem aperiam, eaque ipsa quae ab illo inventore veritatis et quasi architecto beatae vitae dicta sunt explicabo.</p>
</div>
<div class="about-accent"></div>
<div class="about-photo" role="img" aria-label="Photo of a technician servicing an outdoor condenser unit"></div>
<div class="about-text body-copy">
  <p>Sed ut perspiciatis unde omnis iste natus error sit voluptatem accusantium doloremque laudantium, totam rem aperiam, eaque ipsa quae ab illo inventore veritatis et quasi architecto beatae vitae dicta sunt explicabo. Nemo enim ipsam voluptatem quia voluptas sit aspernatur aut odit aut fugit, sed quia consequuntur magni dolores eos qui ratione voluptatem sequi nesciunt. Neque porro quisquam est, qui dolorem ipsum quia dolor sit amet, consectetur, adipisci velit, sed quia non numquam eius modi tempora incidunt ut</p>
  <p>Sed ut perspiciatis unde omnis iste natus error sit voluptatem accusantium doloremque laudantium, totam rem aperiam, eaque ipsa quae ab illo inventore veritatis et quasi architecto beatae vitae dicta sunt explicabo. Nemo enim ipsam voluptatem quia voluptas sit aspernatur aut odit aut fugit, l</p>
</div>
<span class="btn-skew btn-navy" style="left:638px;top:2397px;width:156px;height:54px">Read More</span>

<section class="equipment">
  <h2 class="equipment-title display">Sell Equipment</h2>
  <p class="equipment-text body-copy">Sed ut perspiciatis unde omnis iste natus error sit voluptatem accusantium doloremque laudantium, totam rem aperiam, eaque ipsa quae ab illo inventore veritatis et quasi architecto beatae vitae dicta sunt explicabo. Nemo enim ipsam voluptatem quia voluptas sit aspernatur aut odit aut fugit, sed quia consequuntur magni dolores eos qui ratione voluptatem sequi nesciunt. Neque porro quisquam est, qui dolorem ipsum quia dolor sit amet, consectetur, adipisci velit, sed quia non numquam eius modi tempora incidunt ut labore et dolore magnam aliquam quaerat voluptatem.</p>
  <span class="btn-skew btn-navy" style="left:98px;top:400px;width:156px;height:55px">Buy Now</span>
  <svg class="abs" style="left:590px;top:0" width="610" height="530" viewBox="0 0 610 530" role="img" aria-label="Photo of a blue-grey house with a green lawn at dusk">
    <defs><linearGradient id="houseSky" x1="0" y1="0" x2="0" y2="1"><stop offset="0" stop-color="#8ea5b5"/><stop offset=".55" stop-color="#5f7d92"/><stop offset=".75" stop-color="#557a3a"/><stop offset="1" stop-color="#3f6a28"/></linearGradient></defs>
    <polygon points="110,0 610,0 610,530 110,530 10,265" fill="url(#houseSky)"/>
    <polyline points="110,0 8,265 110,530" fill="none" stroke="#d9232d" stroke-width="5"/>
  </svg>
</section>

<div class="section-head" style="top:3240px">
  <h2 class="section-title display">Our Blog</h2>
</div>

<article class="blog-card" style="left:100px">
  <div class="blog-thumb" role="img" aria-label="Photo of a row of outdoor condenser units" style="background:linear-gradient(180deg,#c7ced6 0%,#8b96a1 60%,#6a7a5e 100%)"><span class="blog-date"><i><svg width="14" height="14" viewBox="0 0 14 14"><rect x="1" y="2" width="12" height="11" fill="none" stroke="#fff" stroke-width="1.5"/><path d="M1 5h12" stroke="#fff" stroke-width="1.5"/></svg></i>06 MAY 2024</span></div>
  <h3 class="blog-title">Dolore eu Fugiat</h3>
  <p class="blog-excerpt">Lorem ipsum dolor sit amet, consectetur adipiscing elit, sed</p>
  <span class="blog-more">READ MORE &nbsp;»</span>
</article>
<article class="blog-card" style="left:438px">
  <div class="blog-thumb" role="img" aria-label="Photo of a technician in a hard hat working on HVAC equipment" style="background:linear-gradient(135deg,#b9c4cf 0%,#7f8f9f 55%,#c9793f 100%)"><span class="blog-date"><i><svg width="14" height="14" viewBox="0 0 14 14"><rect x="1" y="2" width="12" height="11" fill="none" stroke="#fff" stroke-width="1.5"/><path d="M1 5h12" stroke="#fff" stroke-width="1.5"/></svg></i>06 MAY 2024</span></div>
  <h3 class="blog-title">Dolore eu Fugiat Dolore</h3>
  <p class="blog-excerpt">Lorem ipsum dolor sit amet, consectetur adipiscing elit, sed</p>
  <span class="blog-more">READ MORE &nbsp;»</span>
</article>
<article class="blog-card" style="left:777px">
  <div class="blog-thumb" role="img" aria-label="Photo of a family relaxing on a sofa under a wall-mounted AC unit" style="background:linear-gradient(180deg,#e9e6e2 0%,#cfc8c0 55%,#8c8f96 100%)"><span class="blog-date"><i><svg width="14" height="14" viewBox="0 0 14 14"><rect x="1" y="2" width="12" height="11" fill="none" stroke="#fff" stroke-width="1.5"/><path d="M1 5h12" stroke="#fff" stroke-width="1.5"/></svg></i>06 MAY 2024</span></div>
  <h3 class="blog-title">Dolore eu Fugiat Nulla Pariatur</h3>
  <p class="blog-excerpt">Lorem ipsum dolor sit amet, consectetur adipiscing elit, sed</p>
  <span class="blog-more">READ MORE &nbsp;»</span>
</article>

<footer class="site-footer">
  <div class="footer-brand"><span class="brand-mark"></span><span class="brand-name">Coastal Breeze<br>Cooling Company</span></div>
  <h3 class="footer-heading display" style="left:502px">Menu</h3>
  <ul class="footer-menu"><li>Home</li><li>About Us</li><li>Our Services</li><li>Sell Equipment</li><li>Contact Us</li></ul>
  <h3 class="footer-heading display" style="left:752px">Contact Us</h3>
  <ul class="footer-contact">
    <li><svg width="12" height="16" viewBox="0 0 12 16"><path fill="#fff" d="M6 0a6 6 0 00-6 6c0 4.5 6 10 6 10s6-5.5 6-10a6 6 0 00-6-6zm0 8.5A2.5 2.5 0 116 3.5a2.5 2.5 0 010 5z"/></svg><span>2556 enim ipsam voluptatem quia voluptas<br>sit aspernatur aut odit 1522</span></li>
    <li><svg width="16" height="16" viewBox="0 0 24 24"><path fill="#fff" d="M6.6 10.8a15 15 0 006.6 6.6l2.2-2.2c.3-.3.7-.4 1-.2 1.1.4 2.3.6 3.6.6.6 0 1 .4 1 1V20c0 .6-.4 1-1 1A17 17 0 013 4c0-.6.4-1 1-1h3.5c.6 0 1 .4 1 1 0 1.3.2 2.5.6 3.6.1.3 0 .7-.2 1z"/></svg><span>+1 888-888-8888</span></li>
    <li><svg width="16" height="13" viewBox="0 0 14 12"><rect x="1" y="1" width="12" height="10" fill="none" stroke="#fff" stroke-width="1.3"/><path d="M1 1l6 5 6-5" fill="none" stroke="#fff" stroke-width="1.3"/></svg><span>info@coastalbreezecooling.com</span></li>
  </ul>
  <div class="footer-rule"></div>
  <p class="copyright">Copyright ©2024 &nbsp;the Coastal Breeze Cooling All Rights Reserved</p>
  <div class="payments" aria-label="Accepted payment methods"><span></span><span></span><span></span><span></span><span></span><span></span></div>
</footer>

</body>
</html>
```